2 banners on the outside wall of the hall

Banner 1:
KalviMar specializes in the planning, construction, and maintenance of high-quality pond systems, particularly swimming ponds, natural pools, garden ponds, koi ponds, streams, and waterfalls. Learn more at www.kalvimar.de
The following data should be included:
Planning and construction of swimming ponds and natural pools, as well as garden ponds and koi ponds
100% organic
Individually planned
Over 20 years of experience
04627 3150962
www.kalvimar.de
“Logo-KalviMar”
Banner 2:
Grünflut-Laden is the online shop for high-quality aquatic plants for ponds and aquariums.
More information at https://gruenflut-laden.de
Online shop for pond plants and water lilies, as well as aquarium plants and accessories
Over 400 plant species
Top gardener quality
Secure packaging & fast shipping
04627 3150961
www.gruenflut-laden. de
“Logo Greenflow shop”
Here's roughly what we envision:
The designs for each banner should be clearly visible and include everything needed, without appearing cluttered. In other words, it should be immediately clear what the banner is about.
We should also be made aware of our unique selling points and advantages.
It is important that the banners also harmonize visually with each other.
We liked the banner image in the attachment and it serves as inspiration.
The banner print data is produced as follows:
• Banner size: Width x Height: 3880 mm x 1880 mm
• Material: Mesh banner, PVFormat: PDF (X-3:2000)
• Fonts: converted into paths
• Trim allowance: +2 mm all around
• Color space: CMYK
• Resolution: 72 dpi (recommended) at 1:1 resolution
Look and feel
Each slider illustrates characteristics of the customer's brand and the style your logo design should communicate.

```html
<!DOCTYPE html>
<html lang="de">
<head>
<meta charset="utf-8">
<title>KalviMar &amp; Grünflut-Laden – Banner</title>
<link href="https://fonts.googleapis.com/css2?family=Baloo+2:wght@700;800&display=swap" rel="stylesheet">
<style>
  :root {
    --page-bg: #e4e4e2;
    --banner-bg: #eef5f0;
    --brand-blue: #2f5c96;
    --brand-green: #3a9d4a;
    --accent-green: #3e9a5a;
    --pill-text: #ffffff;
    --ornament: #b9d8c0;
  }
  * { box-sizing: border-box; margin: 0; padding: 0; }
  html, body { width: 1200px; height: 900px; overflow: hidden; }
  body {
    background: var(--page-bg);
    font-family: "Baloo 2", system-ui, sans-serif;
    position: relative;
  }
  .banner {
    position: absolute;
    left: 160px;
    width: 880px; height: 426px;
    background: var(--banner-bg);
    overflow: hidden;
  }
  .banner--pond-building { top: 16px; }
  .banner--plant-shop { top: 458px; }
  .banner-shapes { position: absolute; inset: 0; width: 100%; height: 100%; }

  .brand {
    position: absolute;
    left: 540px; top: 26px;
    display: flex; align-items: center; gap: 12px;
  }
  .brand-mark {
    width: 44px; height: 44px;
    background: var(--brand-blue);
    border-radius: 5px;
  }
  .brand-name {
    font-weight: 800;
    font-size: 33px;
    line-height: 1;
    color: var(--brand-blue);
    padding-top: 5px;
    white-space: nowrap;
  }

  .headline {
    position: absolute;
    left: 24px; top: 62px;
    font-weight: 800;
    font-size: 30px;
    line-height: 32px;
    text-transform: uppercase;
    color: var(--brand-blue);
    white-space: nowrap;
  }
  .headline .highlight { color: var(--brand-green); }

  .usp {
    position: absolute;
    left: 22px;
    height: 36px;
    background: var(--brand-green);
    color: var(--pill-text);
    border-radius: 5px;
    font-weight: 800;
    font-size: 19px;
    text-transform: uppercase;
    display: flex; align-items: center;
    padding: 4px 9px 0;
    white-space: nowrap;
  }
  .usp--first { top: 188px; width: 272px; }
  .usp--second { top: 233px; width: 272px; }
  .usp--third { top: 277px; width: 440px; height: 38px; }

  .contact {
    position: absolute;
    left: 24px;
    height: 26px;
    background: var(--brand-blue);
    color: var(--brand-green);
    border-radius: 4px;
    font-weight: 800;
    font-size: 16px;
    display: flex; align-items: center; gap: 5px;
    padding: 2px 8px 0 3px;
    white-space: nowrap;
  }
  .contact--phone { top: 362px; width: 180px; }
  .contact--web { top: 393px; width: 214px; }
  .contact-icon {
    width: 20px; height: 20px; border-radius: 50%;
    background: var(--brand-green);
    display: flex; align-items: center; justify-content: center;
    flex-shrink: 0; margin-top: -2px;
  }
</style>
</head>
<body>

  <!-- Banner 1: pond construction -->
  <section class="banner banner--pond-building">
    <svg class="banner-shapes" viewBox="0 0 1160 562">
      <defs>
        <linearGradient id="swimPondTones" x1="0" y1="0" x2="0.4" y2="1">
          <stop offset="0" stop-color="#7fa35a"/>
          <stop offset="0.35" stop-color="#3f6f7e"/>
          <stop offset="0.7" stop-color="#5e9a8a"/>
          <stop offset="1" stop-color="#8dbb5c"/>
        </linearGradient>
      </defs>
      <path d="M1090 0 L1160 0 L1160 100 C1140 100 1128 78 1114 56 C1100 36 1086 24 1090 0 Z" fill="var(--accent-green)"/>
      <g role="img" aria-label="Leaf sprig ornaments">
        <ellipse cx="40" cy="20" rx="36" ry="16" fill="var(--ornament)" opacity="0.45"/>
        <ellipse cx="350" cy="28" rx="50" ry="24" fill="var(--ornament)" opacity="0.45"/>
        <ellipse cx="870" cy="210" rx="34" ry="30" fill="var(--ornament)" opacity="0.45"/>
        <ellipse cx="780" cy="470" rx="50" ry="34" fill="var(--ornament)" opacity="0.45"/>
      </g>
      <path role="img" aria-label="Photo of a natural swimming pond with clear water, reeds and stone edging"
        d="M860 170 C900 150 960 150 1000 165 C1060 185 1100 150 1160 150 L1160 522 C1050 532 800 532 690 522 C670 480 700 440 740 400 C700 370 660 330 700 290 C740 260 790 270 820 250 C850 230 830 190 860 170 Z"
        fill="url(#swimPondTones)"/>
    </svg>

    <div class="brand">
      <span class="brand-mark"></span>
      <span class="brand-name">KalviMar</span>
    </div>

    <h1 class="headline">
      Planung und Bau von<br>
      <span class="highlight">Schwimmteichen</span> und <span class="highlight">Naturpools</span>,<br>
      sowie Garten- und Koiteichen
    </h1>

    <div class="usp usp--first">100% Biologisch</div>
    <div class="usp usp--second">Individuell geplant</div>
    <div class="usp usp--third">Über 20 Jahre Erfahrung</div>

    <div class="contact contact--phone">
      <span class="contact-icon">
        <svg width="12" height="12" viewBox="0 0 24 24"><path d="M6.6 10.8a15 15 0 0 0 6.6 6.6l2.2-2.2a1 1 0 0 1 1-.25 11.4 11.4 0 0 0 3.6.57 1 1 0 0 1 1 1V20a1 1 0 0 1-1 1A17 17 0 0 1 3 4a1 1 0 0 1 1-1h3.5a1 1 0 0 1 1 1c0 1.25.2 2.45.57 3.57a1 1 0 0 1-.25 1z" fill="#fff"/></svg>
      </span>
      04627 3150962
    </div>
    <div class="contact contact--web">
      <span class="contact-icon">
        <svg width="14" height="14" viewBox="0 0 24 24" fill="none" stroke="#fff" stroke-width="2"><circle cx="12" cy="12" r="9"/><path d="M3 12h18M12 3c3 3 3 15 0 18M12 3c-3 3-3 15 0 18"/></svg>
      </span>
      www.kalvimar.de
    </div>
  </section>

  <!-- Banner 2: aquatic plant shop -->
  <section class="banner banner--plant-shop">
    <svg class="banner-shapes" viewBox="0 0 1160 562">
      <defs>
        <linearGradient id="lilyPondTones" x1="0" y1="0" x2="0.4" y2="1">
          <stop offset="0" stop-color="#6f9a4e"/>
          <stop offset="0.35" stop-color="#3d5a3a"/>
          <stop offset="0.7" stop-color="#6fa54a"/>
          <stop offset="1" stop-color="#8dbb5c"/>
        </linearGradient>
      </defs>
      <path d="M1090 0 L1160 0 L1160 100 C1140 100 1128 78 1114 56 C1100 36 1086 24 1090 0 Z" fill="var(--accent-green)"/>
      <g role="img" aria-label="Leaf sprig ornaments">
        <ellipse cx="40" cy="20" rx="36" ry="16" fill="var(--ornament)" opacity="0.45"/>
        <ellipse cx="350" cy="28" rx="50" ry="24" fill="var(--ornament)" opacity="0.45"/>
        <ellipse cx="870" cy="210" rx="34" ry="30" fill="var(--ornament)" opacity="0.45"/>
        <ellipse cx="780" cy="470" rx="50" ry="34" fill="var(--ornament)" opacity="0.45"/>
      </g>
      <path role="img" aria-label="Photo of a garden pond with water lilies, reeds and stones"
        d="M860 170 C900 150 960 150 1000 165 C1060 185 1100 150 1160 150 L1160 522 C1050 532 800 532 690 522 C670 480 700 440 740 400 C700 370 660 330 700 290 C740 260 790 270 820 250 C850 230 830 190 860 170 Z"
        fill="url(#lilyPondTones)"/>
    </svg>

    <div class="brand">
      <span class="brand-mark"></span>
      <span class="brand-name">Grünflut-Laden</span>
    </div>

    <h1 class="headline">
      Online-Shop für <span class="highlight">Teichpflanzen</span><br>
      und <span class="highlight">Seerosen</span>, sowie<br>
      Aquarienpflanzen und Zubehör
    </h1>

    <div class="usp usp--first">Über 400 Pflanzenarten</div>
    <div class="usp usp--second">Top-Gärtner-Qualität</div>
    <div class="usp usp--third">Sichere Verpackung &amp; schneller Versand</div>

    <div class="contact contact--phone">
      <span class="contact-icon">
        <svg width="12" height="12" viewBox="0 0 24 24"><path d="M6.6 10.8a15 15 0 0 0 6.6 6.6l2.2-2.2a1 1 0 0 1 1-.25 11.4 11.4 0 0 0 3.6.57 1 1 0 0 1 1 1V20a1 1 0 0 1-1 1A17 17 0 0 1 3 4a1 1 0 0 1 1-1h3.5a1 1 0 0 1 1 1c0 1.25.2 2.45.57 3.57a1 1 0 0 1-.25 1z" fill="#fff"/></svg>
      </span>
      04627 3150961
    </div>
    <div class="contact contact--web">
      <span class="contact-icon">
        <svg width="14" height="14" viewBox="0 0 24 24" fill="none" stroke="#fff" stroke-width="2"><circle cx="12" cy="12" r="9"/><path d="M3 12h18M12 3c3 3 3 15 0 18M12 3c-3 3-3 15 0 18"/></svg>
      </span>
      www.gruenflut-laden.de
    </div>
  </section>

</body>
</html>
```